4th Generation Family Business Needs a New Card Design!

We are a family owned 4th Generation company. We are based in the Sydney, Australia area and we are desperately in need of a more modern and classy card. We are monumental masons who design, supply & erect lasting memorials throughout cemeteries in Sydney. Our customers are normally in a period of grieving. I have attached logo files that will need to be implemented on the card. Company was established 1935. Australian Owned and Operated. Card needs to be designed to PIXO.com specification.

Target Market(s)

Our target market is based upon people that a grieving for family members that have passed away. We also deal with alot of companies that own and operate cemeteries.

Industry/Entity Type

Business

Contact Information for Business Card

Simon Harcourt, Operations Manager, 0417293086, simon@harcourtmemorials.com.au
Lewis Harcourt, Director, 0491630572, lewis@harcourtmemorials.com.au
Phone # 02 9561 3048
Website: www.harcourtmemorials.com.au
Address: Suite 17, 8 Palfrey Lane, West Carlow, Sydney NSW 2156

Font styles to use
Serif
Decorative
Script

Requirements
Must have
• Would like to see the logo nicely implemented with a modern design. Embossed lettering would be a nice additive.

```html
<!DOCTYPE html>
<html lang="en">
<head>
<meta charset="utf-8">
<title>Harcourt Memorials – Business Card</title>
<link rel="stylesheet" href="https://fonts.googleapis.com/css2?family=Cinzel:wght@400;600&family=Open+Sans:wght@400&display=swap">
<style>
  :root {
    --backdrop: #a9c0ca;
    --card: #202020;
    --gold: #d9a92a;
    --white: #f2f2f2;
    --silver: #c9c9c9;
  }
  * { box-sizing: border-box; margin: 0; padding: 0; }
  html, body { width: 1200px; height: 829px; overflow: hidden; }
  body {
    background: var(--backdrop);
    display: flex;
    align-items: center;
    justify-content: center;
    gap: 48px;
  }
  .card {
    width: 532px;
    height: 304px;
    background: var(--card);
    border-radius: 3px;
    position: relative;
  }
  /* Front */
  .card-front { display: flex; align-items: center; justify-content: center; }
  .wordmark {
    display: flex; align-items: center; gap: 12px;
    font-family: "Cinzel", serif;
    font-weight: 600;
    color: var(--silver);
    text-align: center;
    line-height: 1.1;
  }
  .wordmark-block { width: 14px; height: 14px; background: var(--silver); }
  .wordmark-name { font-size: 40px; letter-spacing: 2px; }
  .wordmark-sub { display: block; font-size: 20px; letter-spacing: 4px; }
  /* Back */
  .card-back { display: flex; align-items: center; padding: 0 26px 0 30px; }
  .card-back .wordmark { width: 220px; justify-content: center; color: var(--white); }
  .card-back .wordmark-block { width: 10px; height: 10px; background: var(--white); }
  .card-back .wordmark-name { font-size: 24px; letter-spacing: 1px; }
  .card-back .wordmark-sub { font-size: 13px; letter-spacing: 3px; }
  .contact { margin-left: 22px; color: var(--white); font-family: "Open Sans", sans-serif; font-size: 12px; line-height: 1.45; }
  .contact-name { font-family: "Cinzel", serif; font-weight: 600; color: var(--gold); font-size: 17px; letter-spacing: 1px; }
  .contact-title { font-family: "Cinzel", serif; font-size: 12px; letter-spacing: 1.5px; margin-bottom: 4px; }
  .contact-address { margin-bottom: 4px; }
  .contact-line { display: flex; align-items: center; gap: 7px; }
  .contact-line svg { width: 11px; height: 11px; flex: none; fill: var(--gold); }
</style>
</head>
<body>
  <section class="card card-front" aria-label="Card front">
    <div class="wordmark">
      <span class="wordmark-block"></span>
      <div><span class="wordmark-name">HARCOURT</span><span class="wordmark-sub">MEMORIALS</span></div>
    </div>
  </section>

  <section class="card card-back" aria-label="Card back">
    <div class="wordmark">
      <span class="wordmark-block"></span>
      <div><span class="wordmark-name">HARCOURT</span><span class="wordmark-sub">MEMORIALS</span></div>
    </div>
    <div class="contact">
      <p class="contact-name">Simon Harcourt</p>
      <p class="contact-title">OPERATIONS MANAGER</p>
      <p class="contact-address">Suite 17, 8 Palfrey Lane<br>West Carlow, Sydney NSW 2156</p>
      <p class="contact-line"><svg viewBox="0 0 12 12"><path d="M2 1h3l1 3-2 1a7 7 0 0 0 3 3l1-2 3 1v3c-6 0-9-3-9-9z"/></svg>02 9561 3048</p>
      <p class="contact-line"><svg viewBox="0 0 12 12"><path d="M3 0h6a1 1 0 0 1 1 1v10a1 1 0 0 1-1 1H3a1 1 0 0 1-1-1V1a1 1 0 0 1 1-1zm0 2v8h6V2z"/></svg>0417293086</p>
      <p class="contact-line"><svg viewBox="0 0 12 12"><path d="M0 2h12v8H0zm1 1v.5l5 3.5 5-3.5V3z"/></svg>simon@harcourtmemorials.com.au</p>
      <p class="contact-line"><svg viewBox="0 0 12 12"><circle cx="6" cy="6" r="6"/></svg>www.harcourtmemorials.com.au</p>
    </div>
  </section>
</body>
</html>
```